CD covers for a melodic death metal band from Quebec City, Canada *

We are a small band named "Brovenka" and this is our first project with our own material. We plan to put our music on every platform available.Even though we know we are a small scale band, we are very proud of what we've done and we want the best covers possible to represent our work.This project consists of 2 album covers, part I and part II, but considered as a single project. We are really open to any design ideas but we really think that an album cover should represent the genre, the energy and the atmosphere of the music it presents. That's why we plan to release those albums one after the other separately, because they both have their own vibe. But to keep both parts as a whole entity, we thought of having the exact same image/representation/theme on both album covers, but with a different feel and ambiance for each of them.By keeping everything(logo, title, etc) at the same place, the emphasis of the covers should be in those differences. The Part I is more aggressive, fast tempo and "in your face". The Part II is more melodic, melancolic and dark. Our lyrical theme is oriented around the different flaws of humanity (Anger, Sorrow, Loneliness, Delusion). A lot of things that touches humanity. We put in attachments 2 song previews for each part, as reference. Note that these are not the final versions, as we are still in the recording/mixing process. We also put our logo, as we would like it to be present on both covers. You can adjust the background/border color as you see fit. We'd also like to have our name "Brovenka" and "I" and "II" as album titles somewhere in the design, on any font/color you think is best.Thank you and we are very eager to see your ideas!

```html
<!DOCTYPE html>
<html lang="en">
<head>
<meta charset="utf-8">
<title>Brovenka — Part II cover</title>
<link rel="stylesheet" href="https://fonts.googleapis.com/css2?family=Montserrat:wght@400;600;700;800&family=Roboto+Condensed:wght@400;700&display=swap">
<style>
  :root {
    --bg: #000000;
    --label: #5a5a5a;
    --label-soft: #3c3c3c;
    --ink: #ffffff;
    --ink-soft: #e6e6e6;
    --stone: #b9aca0;
    --sky-top: #1c1a18;
    --sky-mid: #2b2724;
    --ground: #2a2622;
    --ground-deep: #151312;
    --teal: #3fc7c2;
    --emblem-stone: #5a5550;
  }
  * { margin: 0; padding: 0; box-sizing: border-box; }
  html, body { width: 1200px; height: 1200px; overflow: hidden; background: var(--bg); }
  .sheet { position: relative; width: 1200px; height: 1200px; background: var(--bg); font-family: "Montserrat", Arial, sans-serif; }

  .sheet-title { position: absolute; left: 42px; top: 70px; font-family: "Roboto Condensed", Arial, sans-serif; font-size: 20px; color: var(--label); letter-spacing: 0.2px; }
  .sheet-title strong { font-weight: 700; }
  .sheet-title span { font-weight: 400; font-size: 17px; }

  .sheet-code { position: absolute; left: 41px; top: 212px; transform: rotate(-90deg); transform-origin: left top; font-family: "Roboto Condensed", Arial, sans-serif; font-size: 12px; color: var(--label-soft); }

  .panel { position: absolute; top: 326px; width: 550px; height: 548px; overflow: hidden; }
  .panel--back { left: 43px; }
  .panel--front { left: 607px; }

  .scene { position: absolute; inset: 0;
    background:
      radial-gradient(ellipse 60% 8% at 50% 54%, rgba(143,198,207,0.55), transparent 70%),
      linear-gradient(180deg, var(--sky-top) 0%, var(--sky-mid) 35%, #24221f 48%, #5d7a80 55%, #4a4744 64%, var(--ground) 67%, var(--ground-deep) 100%);
  }
  .scene--front {
    background:
      radial-gradient(ellipse 60% 8% at 30% 54%, rgba(143,198,207,0.45), transparent 70%),
      linear-gradient(180deg, #2a2825 0%, #3a3531 20%, #24221f 48%, #556f74 55%, #4a4744 64%, var(--ground) 67%, var(--ground-deep) 100%);
  }

  .emblem { position: absolute; left: 117px; top: 146px; width: 340px; height: 328px; border-radius: 46% 46% 40% 40%;
    background:
      radial-gradient(ellipse 42% 46% at 50% 50%, var(--emblem-stone) 0%, rgba(90,85,80,0.9) 38%, transparent 62%),
      radial-gradient(ellipse 50% 50% at 50% 50%, rgba(63,199,194,0.75) 0%, rgba(63,199,194,0.45) 55%, transparent 72%);
  }

  .tracklist { position: absolute; left: 0; right: 0; top: 95px; text-align: center; color: var(--ink-soft); font-size: 8.5px; letter-spacing: 0.6px; }
  .tracklist-title { font-size: 10.5px; font-weight: 600; letter-spacing: 1px; margin-bottom: 12px; }
  .tracklist ol { list-style: none; line-height: 14.6px; }
  .tracklist-more { margin-top: 6px; font-size: 12px; font-weight: 700; }

  .name-block { position: absolute; left: 0; right: 0; text-align: center; color: var(--ink); }
  .name-block .name { font-weight: 800; text-transform: uppercase; line-height: 1; }
  .name-block .part { font-weight: 600; letter-spacing: 3px; }
  .name-block--back { top: 480px; }
  .name-block--back .name { font-size: 17px; }
  .name-block--back .part { font-size: 7px; margin-top: 3px; }

  .front-name { position: absolute; left: 0; right: 0; top: 40px; text-align: center; color: var(--stone); opacity: 0.82; font-weight: 800; font-size: 82px; text-transform: uppercase; letter-spacing: -1px; line-height: 1; }

  .spine { position: absolute; z-index: 2; left: 596px; top: 845px; transform: rotate(-90deg); transform-origin: left top; color: var(--ink); font-size: 6.5px; line-height: 8px; letter-spacing: 1.6px; font-weight: 600; white-space: nowrap; }

  .name-block--sheet { top: 1050px; }
  .name-block--sheet .name { font-size: 32px; }
  .name-block--sheet .part { font-size: 11px; letter-spacing: 4px; margin-top: 6px; }
</style>
</head>
<body>
<main class="sheet">
  <p class="sheet-title"><strong>BROVENKA _</strong> <span>PART II</span></p>
  <p class="sheet-code">Cover_001</p>

  <section class="panel panel--back">
    <div class="scene" role="img" aria-label="Dark stormy sky over a cracked barren plain, pale blue light breaking through the clouds at the horizon"></div>
    <div class="tracklist">
      <p class="tracklist-title">XXX XXXXXX XXXXX</p>
      <ol>
        <li>01. XXXX XXXXXX XX</li>
        <li>02. XXXXXX XXXXXXXX XXXXX</li>
        <li>03. XXX XXXXX XX XXXXX</li>
        <li>04. XXXXXXX XXX</li>
        <li>05. XXXXX XX XXXXX X</li>
      </ol>
      <p class="tracklist-more">...</p>
    </div>
    <div class="name-block name-block--back">
      <p class="name">Brovenka</p>
      <p class="part">PART II</p>
    </div>
  </section>

  <section class="panel panel--front">
    <div class="scene scene--front" role="img" aria-label="Stormy sky over a cracked wasteland"></div>
    <p class="front-name">Brovenka</p>
    <div class="emblem" role="img" aria-label="Carved stone emblem wrapped in teal flames standing on the plain"></div>
  </section>

  <p class="spine">BROVENKA _ PART II</p>

  <div class="name-block name-block--sheet">
    <p class="name">Brovenka</p>
    <p class="part">PART II</p>
  </div>
</main>
</body>
</html>
```